Stationery Design Project

I need a stationary design for our company. we are based in Houston, TX and we are called Mira Vell Lending. And we are wanting to brand our MoneyMendPlus program, which includes our tax preparation and restoration, credit repair service. Although our business offers other programs, we are interested in mainly focusing on The MoneyMendPlus program. We are looking for way to brand our ourselves and I believe that a great stationery design will help in achieving this goal. Our logo design is blue and light blue. the slogan is orange.

Industry/Entity Type

Business

Requirements
Must have
• Address: 30871 Calloway Ln. B-22
Houston, TX 75419
Tel. 555-318-6207
Fax 555-294-7153
www.miravelllending.example
info@miravelllending.example
Our Slogan: Happiness, Restored!

```html
<!DOCTYPE html>
<html lang="en">
<head>
<meta charset="utf-8">
<title>Mira Vell Lending – Business Card Set</title>
<link rel="stylesheet" href="https://fonts.googleapis.com/css2?family=Arimo:wght@400&family=Tinos:wght@400&display=swap">
<style>
  :root {
    --backdrop: #e8e3dc;
    --label: #2a2622;
    --card-black: #050505;
    --card-navy: #123e66;
    --card-white: #ffffff;
    --brand-blue: #2e72b8;
    --mark-fill: #3f7fc0;
    --mark-fill-soft: #5b8fc4;
    --frame-light: #c9def0;
    --slogan-orange: #f0962a;
    --ink-light: #ffffff;
    --ink-grey: #3a3a3a;
    --rule: #3c3c3c;
  }
  * { margin: 0; padding: 0; box-sizing: border-box; }
  html, body { width: 1200px; height: 800px; overflow: hidden; }
  body {
    position: relative;
    background: var(--backdrop);
    font-family: "Arimo", Arial, sans-serif;
  }
  .view-label {
    position: absolute;
    width: 510px;
    text-align: center;
    font-size: 21px;
    color: var(--label);
  }
  .card {
    position: absolute;
    width: 510px;
    height: 290px;
    border-radius: 22px;
    box-shadow: 0 4px 12px rgba(0,0,0,0.25);
    overflow: hidden;
  }
  .card--front { left: 70px; top: 90px; background: var(--card-black); }
  .card--back-white { left: 620px; top: 90px; background: var(--card-white); }
  .card--back-navy { left: 75px; top: 450px; background: var(--card-navy); }
  .card--back-framed { left: 620px; top: 450px; background: var(--card-navy); }

  .mark-square {
    position: absolute;
    background: var(--mark-fill);
  }
  .mark-square--front { left: 140px; top: 36px; width: 60px; height: 60px; background: var(--brand-blue); }
  .mark-square--box { left: 57px; top: 34px; width: 52px; height: 52px; background: var(--mark-fill-soft); }
  .mark-square--large { left: 215px; top: 50px; width: 80px; height: 80px; background: var(--mark-fill-soft); }

  .program-name {
    position: absolute;
    left: 38px;
    top: 100px;
    font-family: "Tinos", "Times New Roman", serif;
    font-size: 37px;
    color: var(--brand-blue);
    letter-spacing: -0.5px;
  }
  .slogan {
    position: absolute;
    right: 22px;
    top: 198px;
    font-family: "Tinos", "Times New Roman", serif;
    font-size: 22px;
    font-variant: small-caps;
    letter-spacing: 0.5px;
    color: var(--slogan-orange);
  }
  .front-rule {
    position: absolute;
    left: 28px; right: 22px;
    top: 231px;
    height: 1px;
    background: var(--rule);
  }
  .contact {
    position: absolute;
    top: 238px;
    font-size: 12.5px;
    line-height: 18px;
    color: var(--ink-light);
  }
  .contact--phones { left: 30px; }
  .contact--online { left: 155px; }
  .contact--address { right: 22px; text-align: right; }
  .contact-line { display: flex; align-items: center; gap: 7px; white-space: nowrap; }
  .contact-line svg { width: 10px; height: 10px; flex: none; }

  .lender-box {
    position: absolute;
    font-family: "Tinos", "Times New Roman", serif;
    color: var(--ink-light);
    font-size: 14.5px;
  }
  .lender-box--filled {
    left: 172px; top: 33px;
    width: 171px; height: 171px;
    background: var(--card-navy);
    border: 2px solid var(--frame-light);
    outline: 4px solid var(--card-navy);
    outline-offset: -8px;
  }
  .lender-box--outlined {
    left: 171px; top: 36px;
    width: 169px; height: 169px;
    border: 4px solid var(--frame-light);
  }
  .lender-box .lender-name {
    position: absolute;
    left: 0; right: 0;
    bottom: 30px;
    text-align: center;
    white-space: nowrap;
  }
  .lender-name--large {
    position: absolute;
    left: 0; right: 0;
    top: 180px;
    text-align: center;
    font-family: "Tinos", "Times New Roman", serif;
    font-size: 22px;
    color: var(--ink-light);
  }
  .web-address {
    position: absolute;
    left: 0; right: 0;
    top: 250px;
    text-align: center;
    font-size: 19px;
    letter-spacing: 2.2px;
    color: var(--ink-light);
  }
  .card--back-white .web-address { color: var(--ink-grey); top: 240px; }
</style>
</head>
<body>

  <div class="view-label" style="left:70px; top:50px;">Front</div>
  <div class="view-label" style="left:620px; top:50px;">Back - 1</div>
  <div class="view-label" style="left:75px; top:410px;">Back - 2</div>
  <div class="view-label" style="left:620px; top:410px;">Back - 3</div>

  <section class="card card--front" aria-label="Card front">
    <div class="mark-square mark-square--front" role="img" aria-label="MoneyMendPlus program mark"></div>
    <div class="program-name">MoneyMendPlus</div>
    <div class="slogan">Happiness, Restored!</div>
    <div class="front-rule"></div>

    <div class="contact contact--phones">
      <div class="contact-line">
        <svg viewBox="0 0 10 10" aria-hidden="true"><path d="M2 1l2 2-1 1.3c.6 1.2 1.5 2.1 2.7 2.7L7 6l2 2-1.2 1.4C4.5 9 1 5.5.6 2.2z" fill="#fff"/></svg>
        555-318-6207
      </div>
      <div class="contact-line">
        <svg viewBox="0 0 10 10" aria-hidden="true"><rect x="2.5" y="0.5" width="5" height="3" fill="#fff"/><rect x="0.5" y="3.5" width="9" height="4" rx="1" fill="#fff"/><rect x="2.5" y="7" width="5" height="2.5" fill="#fff"/></svg>
        555-294-7153
      </div>
    </div>

    <div class="contact contact--online">
      <div class="contact-line">
        <svg viewBox="0 0 10 10" aria-hidden="true"><rect x="0.5" y="2" width="9" height="6.5" fill="#fff"/><path d="M0.8 2.3L5 5.6l4.2-3.3" fill="none" stroke="#050505" stroke-width="1"/></svg>
        info@miravelllending.example
      </div>
      <div class="contact-line">
        <svg viewBox="0 0 10 10" aria-hidden="true"><circle cx="5" cy="5" r="4.3" fill="none" stroke="#fff" stroke-width="1"/><ellipse cx="5" cy="5" rx="1.8" ry="4.3" fill="none" stroke="#fff" stroke-width="0.8"/><path d="M0.7 5h8.6" stroke="#fff" stroke-width="0.8"/></svg>
        www.miravelllending.example
      </div>
    </div>

    <div class="contact contact--address">
      <div>30871 Calloway Ln. B-22</div>
      <div>Houston, TX 75419</div>
    </div>
  </section>

  <section class="card card--back-white" aria-label="Card back, white version">
    <div class="lender-box lender-box--filled">
      <div class="mark-square mark-square--box" role="img" aria-label="Mira Vell Lending mark"></div>
      <div class="lender-name">Mira Vell Lending</div>
    </div>
    <div class="web-address">www.miravelllending.example</div>
  </section>

  <section class="card card--back-navy" aria-label="Card back, navy version">
    <div class="mark-square mark-square--large" role="img" aria-label="Mira Vell Lending mark"></div>
    <div class="lender-name--large">Mira Vell Lending</div>
    <div class="web-address">www.miravelllending.example</div>
  </section>

  <section class="card card--back-framed" aria-label="Card back, framed navy version">
    <div class="lender-box lender-box--outlined">
      <div class="mark-square mark-square--box" role="img" aria-label="Mira Vell Lending mark" style="left:55px; top:30px;"></div>
      <div class="lender-name">Mira Vell Lending</div>
    </div>
    <div class="web-address">www.miravelllending.example</div>
  </section>

</body>
</html>
```